Communication and Marketing agency needs a new presentation card

We are a group of communication and marketing agencies specialized in companies that are in the logistics and industrial sector. The head agency is TELVANO Grupo and the group consists of 4 agencies: TELVANO Media, TELVANO Digital, TELVANO Research and DifundeEnPantalla. We hace 4 offices in Spain (Madrid, Barcelona, Valencia and Murcia). We are looking for a clean and attractive design that transmits our experience, brand presence in the market and knowledge to those who receive the card.It has to maintain the colors of the logo that is attached.
Target Market(s)
logistics and industrial sector
Marketing department
Contact Information for Business Card
Clean and attractive design

```html
<!DOCTYPE html>
<html lang="es">
<head>
<meta charset="utf-8">
<title>TELVANO Grupo – Tarjeta de visita</title>
<link rel="stylesheet" href="https://fonts.googleapis.com/css2?family=Montserrat:wght@400;500;600;700&display=swap">
<style>
  :root {
    --stage: #1b1e23;
    --card-dark: #2b2826;
    --brand-red: #b41d27;
    --paper: #ffffff;
    --ink: #1f1f1f;
    --arc: #231f1e;
    --map-grey: #b9b9b9;
    --soft-grey: #bdbdbd;
  }
  * { margin: 0; padding: 0; box-sizing: border-box; }
  html, body {
    width: 1200px; height: 738px; overflow: hidden;
    background: var(--stage);
    font-family: "Montserrat", sans-serif;
  }
  .stage {
    position: relative; width: 1200px; height: 738px;
    display: flex; align-items: center; justify-content: center; gap: 40px;
  }
  .card {
    position: relative; width: 520px; height: 336px; border-radius: 4px; overflow: hidden;
    box-shadow: 0 14px 30px rgba(0,0,0,.45);
  }

  /* Back side */
  .card--back { background: var(--card-dark); }
  .agency-grid {
    position: absolute; inset: 0;
    display: grid; grid-template-columns: 1fr 1fr; grid-template-rows: 1fr 1fr;
    padding: 100px 56px; row-gap: 10px; column-gap: 20px;
    align-items: center; justify-items: center;
  }
  .agency-name {
    font-weight: 700; font-size: 17px; letter-spacing: .4px; line-height: 1;
    text-align: center; white-space: nowrap;
  }
  .agency-name--red { color: var(--brand-red); }
  .agency-name--white { color: var(--paper); }

  /* Front side */
  .card--front { background: var(--brand-red); }
  .card-shape { position: absolute; inset: 0; }
  .group-name {
    position: absolute; left: 36px; top: 46px;
    color: var(--paper); font-weight: 700; font-size: 21px; letter-spacing: .4px; line-height: 1;
    white-space: nowrap;
  }
  .person { position: absolute; left: 42px; top: 126px; color: var(--paper); }
  .person-name { font-size: 17px; font-weight: 400; letter-spacing: .5px; white-space: nowrap; }
  .person-name strong { font-weight: 700; }
  .person-role { font-size: 11px; margin-top: 4px; letter-spacing: .4px; }
  .contact-list {
    position: absolute; left: 42px; top: 214px; list-style: none; color: var(--paper);
    font-size: 12.5px; letter-spacing: .4px;
  }
  .contact-list li { display: flex; align-items: center; gap: 9px; height: 18px; white-space: nowrap; }
  .contact-icon { width: 9px; height: 9px; flex: none; }
  .map-area {
    position: absolute; left: 292px; top: 52px; width: 180px; height: 150px;
    border-radius: 10px;
    background: radial-gradient(ellipse at center, #9a9a9a 0%, var(--map-grey) 65%, rgba(185,185,185,0) 100%);
  }
  .office-list {
    position: absolute; left: 282px; top: 224px;
    font-size: 11px; font-weight: 600; color: var(--ink); letter-spacing: .2px; white-space: nowrap;
  }
  .office-list .sep { color: var(--brand-red); padding: 0 3px; }
</style>
</head>
<body>
<main class="stage">

  <section class="card card--back" aria-label="Reverso de la tarjeta">
    <div class="agency-grid">
      <p class="agency-name agency-name--red">TELVANO Media</p>
      <p class="agency-name agency-name--white">TELVANO Research</p>
      <p class="agency-name agency-name--white">TELVANO Digital</p>
      <p class="agency-name agency-name--red">DifundeEnPantalla</p>
    </div>
  </section>

  <section class="card card--front" aria-label="Anverso de la tarjeta">
    <svg class="card-shape" width="520" height="336" viewBox="0 0 520 336" aria-hidden="true">
      <circle cx="400" cy="144" r="175" fill="var(--arc)"/>
      <circle cx="410" cy="140" r="172" fill="var(--paper)"/>
      <rect x="410" y="0" width="110" height="300" fill="var(--paper)"/>
    </svg>

    <p class="group-name">TELVANO Grupo</p>

    <div class="person">
      <p class="person-name"><strong>Julián</strong> Ortega</p>
      <p class="person-role">Director</p>
    </div>

    <ul class="contact-list">
      <li>
        <svg class="contact-icon" viewBox="0 0 10 10" aria-hidden="true"><path d="M2 1l2 2-1 1.2c.6 1.2 1.6 2.2 2.8 2.8L7 6l2 2-1.4 1.4C4.5 9 1 5.5.6 2.4z" fill="currentColor"/></svg>
        910 472 318
      </li>
      <li>
        <svg class="contact-icon" viewBox="0 0 10 10" aria-hidden="true"><rect x="2.5" y=".5" width="5" height="9" rx="1" fill="none" stroke="currentColor" stroke-width="1.2"/><circle cx="5" cy="7.8" r=".6" fill="currentColor"/></svg>
        611 905 274
      </li>
      <li>
        <svg class="contact-icon" viewBox="0 0 10 10" aria-hidden="true"><rect x=".6" y="2" width="8.8" height="6" fill="none" stroke="currentColor" stroke-width="1.1"/><path d="M.6 2L5 5.5 9.4 2" fill="none" stroke="currentColor" stroke-width="1.1"/></svg>
        jortega@telvano.es
      </li>
      <li>
        <svg class="contact-icon" viewBox="0 0 10 10" aria-hidden="true"><circle cx="5" cy="5" r="4.3" fill="none" stroke="currentColor" stroke-width="1"/><ellipse cx="5" cy="5" rx="1.8" ry="4.3" fill="none" stroke="currentColor" stroke-width=".8"/><path d="M.7 5h8.6" stroke="currentColor" stroke-width=".8"/></svg>
        www.telvano.es
      </li>
      <li>
        <svg class="contact-icon" viewBox="0 0 10 10" aria-hidden="true"><rect x="1" y="1" width="8" height="8" fill="currentColor"/></svg>
        julianortega
      </li>
    </ul>

    <div class="map-area" role="img" aria-label="Mapa de puntos de España con las cuatro oficinas marcadas"></div>

    <p class="office-list">Madrid<span class="sep">|</span>Barcelona<span class="sep">|</span>Valencia<span class="sep">|</span>Murcia</p>
  </section>

</main>
</body>
</html>
```